Overview of Elder Abuse Resources Brochure

We need a 2-page brochure that provides a list of resources for elders in tribal communities in the US and those who care for them. We want it to be simple and easy to read, and easy to see the difference between each resource. We would also like eye-catching images or graphics. Please keep the images on the front, and add any photos or graphics that depict Native American elders. We need both of our logos on the first page, in the far-right column. Please refer to the attached image for our brand colors and a font suggestion. Please keep the three columns on each page, but delete the blank pages in the document.

```html
<!DOCTYPE html>
<html lang="en">
<head>
<meta charset="utf-8">
<title>Services for Elders – Tri-fold Brochure</title>
<link href="https://fonts.googleapis.com/css2?family=Poppins:ital,wght@0,400;0,500;0,600;0,700;1,600&display=swap" rel="stylesheet">
<style>
  :root{
    --backdrop:#5e5e5f;
    --brick:#9f4845;
    --brick-soft:#b55c53;
    --brick-text:#b5524c;
    --teal:#4aa8b0;
    --teal-deep:#187d86;
    --teal-text:#43a0a8;
    --ink:#1d1d1d;
    --paper:#ffffff;
    --paper-shade:#d9dadb;
  }
  *{margin:0;padding:0;box-sizing:border-box;}
  html,body{width:838px;height:1200px;overflow:hidden;}
  body{background:var(--backdrop);font-family:"Poppins",sans-serif;color:var(--ink);position:relative;}

  .sheet{position:absolute;left:118px;width:596px;height:461px;display:flex;}
  .sheet--outside{top:99px;}
  .sheet--inside{top:614px;}
  .panel{position:relative;width:199px;height:100%;overflow:hidden;}
  .panel--blank,.panel--paper{background:linear-gradient(90deg,var(--paper-shade) 0%,#f3f3f4 35%,var(--paper) 70%);}
  .panel svg.backdrop{position:absolute;inset:0;width:100%;height:100%;}
  .abs{position:absolute;}

  /* Outside, back panel */
  .respect__title{left:15px;top:20px;color:#fff;font-size:12.5px;font-weight:500;}
  .respect__body{left:15px;top:46px;width:168px;color:#fff;font-size:7.6px;line-height:9.1px;}
  .respect__body p{margin-bottom:9px;}
  .contact{left:15px;top:216px;color:#fff;}
  .contact__label{font-size:7.6px;}
  .contact__name{font-size:9px;font-weight:600;line-height:11px;}
  .locator{left:0;width:199px;top:308px;text-align:center;color:#fff;font-size:9px;font-weight:600;line-height:11px;}
  .callout{display:inline-block;background:var(--brick-soft);color:#fff;font-weight:600;font-size:9px;padding:3px 0;text-align:center;}
  .locator .callout{width:76px;margin-top:4px;}
  .quick-list{left:15px;top:380px;width:169px;color:#fff;font-size:7.6px;line-height:9px;}
  .quick-list li{list-style:none;display:flex;justify-content:space-between;padding:4px 0;border-bottom:1px solid var(--brick-soft);}
  .quick-list li:last-child{border-bottom:none;}

  /* Cover */
  .cover__title{left:20px;top:16px;color:#fff;font-size:17.5px;font-weight:600;line-height:20px;}
  .cover__sub{left:20px;top:36px;color:#fff;font-size:10px;font-weight:600;}
  .cover__who{left:20px;top:51px;color:#fff;font-size:9px;line-height:11px;}
  .partner{left:15px;color:#fff;font-size:9px;font-weight:600;display:flex;align-items:center;gap:6px;}
  .partner__mark{width:14px;height:14px;background:#fff;flex:none;}
  .partner--one{top:282px;}
  .partner--two{top:318px;}
  .cover__ask{left:15px;width:180px;color:#fff;font-size:12.5px;font-weight:600;font-style:italic;line-height:14px;}
  .cover__ask--one{top:352px;}
  .cover__ask--two{top:388px;}
  .cover__note{left:15px;top:424px;color:#fff;font-size:8px;line-height:9px;}

  /* Inside, stories */
  .stories__title{left:29px;top:28px;color:var(--teal-text);font-size:14.5px;font-weight:700;line-height:16.5px;}
  .stories__list{left:27px;top:68px;width:165px;list-style:none;font-size:7.7px;line-height:9px;}
  .stories__list li{position:relative;padding-left:19px;margin-bottom:9.6px;}
  .stories__list li::before,.stories__list li::after{content:"";position:absolute;background:var(--teal);}
  .stories__list li::before{left:0;top:6px;width:14px;height:1.2px;}
  .stories__list li::after{left:6.4px;top:0;width:1.2px;height:14px;}
  .stories__help{left:46px;top:243px;font-size:7.7px;}
  .stories__call{left:46px;top:261px;width:90px;}

  /* Inside, resource columns */
  .resources{position:absolute;left:10px;top:29px;width:177px;}
  .resources__title{font-size:14.5px;font-weight:700;line-height:16px;}
  .resources--elders .resources__title{color:var(--teal-text);}
  .resources--care .resources__title{color:#fff;}
  .resource{margin-top:9px;}
  .resource__name{font-size:11px;font-weight:500;line-height:12.5px;padding-bottom:2px;border-bottom:1px solid var(--teal);margin-bottom:4px;}
  .resources--elders .resource__name{color:var(--brick-text);}
  .resources--care .resource__name{color:#fff;border-bottom-color:#fff;}
  .resource p{font-size:7.6px;line-height:9px;}
  .resource p + p{margin-top:6px;}
  .resources--care .resource p{color:#fff;}
  .panel--care{background:linear-gradient(180deg,#b0534d 0%,#b65e54 100%);}
</style>
</head>
<body>

<section class="sheet sheet--outside" aria-label="Brochure outside">
  <div class="panel panel--respect">
    <svg class="backdrop" viewBox="0 0 199 461" preserveAspectRatio="none">
      <defs>
        <linearGradient id="respect-photo" x1="0" y1="0" x2="1" y2="0.6">
          <stop offset="0" stop-color="#9c4543"/>
          <stop offset="0.7" stop-color="#a24d4a"/>
          <stop offset="1" stop-color="#8d4547"/>
        </linearGradient>
      </defs>
      <rect width="199" height="461" fill="var(--teal)"/>
      <polygon points="0,0 199,0 199,157 0,201" fill="url(#respect-photo)" role="img" aria-label="Tinted photograph of an elder seen in profile"/>
    </svg>
    <h2 class="abs respect__title">Respect for Elders</h2>
    <div class="abs respect__body">
      <p>Do you have concerns about an Elder, maybe you see that they are not taking care of themselves, or family only comes once a month when the Elder has money?</p>
      <p>Is an Elder telling you that they are not treated with respect or that someone is bothering them?</p>
      <p>These may be signs of Elder abuse, neglect or exploitation.</p>
    </div>
    <div class="abs contact">
      <p class="contact__label">For help contact:</p>
      <p class="contact__name">Your Tribal Social Services or Elders Department</p>
    </div>
    <div class="abs locator">
      <p>The Elder Care Finder for information<br>on Adult Protective Services</p>
      <span class="callout">1-800-555-0142</span>
    </div>
    <ul class="abs quick-list">
      <li><span>If a serious emergency</span><span>call 911</span></li>
      <li><span>For mental health support<br>for yourself or an Elder</span><span>call or text 555-0188</span></li>
      <li><span>Domestic Violence<br>Hotline</span><span>1.800.555.0199</span></li>
    </ul>
  </div>

  <div class="panel panel--blank"></div>

  <div class="panel panel--cover">
    <svg class="backdrop" viewBox="0 0 199 461" preserveAspectRatio="none">
      <defs>
        <linearGradient id="cover-photo" x1="0" y1="0" x2="0.6" y2="1">
          <stop offset="0" stop-color="#c9473d"/>
          <stop offset="0.35" stop-color="#c9a48f"/>
          <stop offset="0.7" stop-color="#b6473a"/>
          <stop offset="1" stop-color="#6f7a4c"/>
        </linearGradient>
      </defs>
      <rect width="199" height="461" fill="var(--teal)"/>
      <polygon points="0,0 199,0 199,204 0,154" fill="var(--brick)"/>
      <polygon points="0,154 199,204 199,266 0,220" fill="var(--teal-deep)"/>
      <polygon points="48,96 120,78 199,92 199,266 44,230" fill="url(#cover-photo)" role="img" aria-label="Photograph of a smiling elder woman in a beaded headdress and necklaces"/>
    </svg>
    <h1 class="abs cover__title">Services for Elders</h1>
    <p class="abs cover__sub">&amp; People Who Care for Them</p>
    <p class="abs cover__who">My Mother • My Father • My Sister<br>My Grandchild • Myself</p>
    <p class="abs partner partner--one"><span class="partner__mark"></span>Alliance for Indigenous Elders</p>
    <p class="abs partner partner--two"><span class="partner__mark"></span>Tribal Elder Justice Network</p>
    <p class="abs cover__ask cover__ask--one">Are you caring for an Elder or a Grandchild?</p>
    <p class="abs cover__ask cover__ask--two">Are you an Elder who needs help staying at home?</p>
    <p class="abs cover__note">These programs and information can<br>be a helpful resource</p>
  </div>
</section>

<section class="sheet sheet--inside" aria-label="Brochure inside">
  <div class="panel panel--paper panel--stories">
    <svg class="backdrop" viewBox="0 0 199 461" preserveAspectRatio="none">
      <defs>
        <linearGradient id="stories-photo" x1="0" y1="0" x2="1" y2="1">
          <stop offset="0" stop-color="#9d403e"/>
          <stop offset="0.6" stop-color="#b0524c"/>
          <stop offset="1" stop-color="#7d3434"/>
        </linearGradient>
      </defs>
      <polygon points="0,335 199,289 199,305 0,350" fill="var(--teal)"/>
      <polygon points="0,350 199,305 199,461 0,461" fill="url(#stories-photo)" role="img" aria-label="Tinted photograph of an elder woman wrapped in a blanket"/>
    </svg>
    <h2 class="abs stories__title">Do these stories sound<br>familiar to you?</h2>
    <ul class="abs stories__list">
      <li>My mother gets lost driving<br>home from the store.</li>
      <li>I need help getting groceries<br>and with chores at home.</li>
      <li>My sister is raising 3<br>grandchildren on her own.</li>
      <li>My dad wants to sleep all the time; he doesn’t go out with friends anymore. He stopped drumming.</li>
      <li>My son is disrespecting me.<br>He only comes to visit when<br>my retirement money arrives.<br>He always asks for money</li>
    </ul>
    <p class="abs stories__help">Help is available…</p>
    <span class="abs callout stories__call">1-800-555-0142</span>
  </div>

  <div class="panel panel--paper">
    <div class="resources resources--elders">
      <h2 class="resources__title">Resources for Elders</h2>
      <div class="resource" style="margin-top:13px">
        <h3 class="resource__name">Elder Care Finder</h3>
        <p>Call or Text: 1-800-555-0142<br>Email: help@eldercarefinder.org<br>https://eldercarefinder.org/home<br>For help finding support.<br>Ask about services to Tribal Elders.</p>
      </div>
      <div class="resource">
        <h3 class="resource__name">National Memory Care Line</h3>
        <p>Call 1-800-555-0177<br>(24 hours 7 days a week)<br>For support for people living with dementia, caregivers, families and the public.<br>Connect with a live person who can provide information, local resources, crisis assistance and emotional support.</p>
      </div>
      <div class="resource">
        <h3 class="resource__name">24/7 Crisis Support Line</h3>
        <p>For mental health support, call or text 555-0188.</p>
      </div>
      <div class="resource">
        <h3 class="resource__name">State &amp; Tribal Hotlines | Native</h3>
        <p>Tribal Elder Justice Network<br>To find local resources within your tribe or state that specialize in elder abuse, neglect or exploitation,</p>
        <p>https://indigenouselders.org/tejn/<br>state-tribal-hotlines/</p>
      </div>
      <div class="resource">
        <h3 class="resource__name">Circle of Care Native Helpline</h3>
        <p>A 24/7 safe, confidential and anonymous domestic and sexual violence helpline for Native Americans and Alaska Natives.</p>
        <p>Call 1-844-555-0163</p>
        <p>https://circleofcarehelpline.org/</p>
      </div>
    </div>
  </div>

  <div class="panel panel--care">
    <div class="resources resources--care">
      <h2 class="resources__title">Resources for Caregivers<br>Caring for an Older Adult</h2>
      <div class="resource" style="margin-top:10px">
        <h3 class="resource__name">Elder Care Finder</h3>
        <p>Call or Text: 1-800-555-0142<br>Email: help@eldercarefinder.org<br>https://eldercarefinder.org/home</p>
        <p>For help finding support. Ask about<br>services to Tribal Elders.</p>
      </div>
      <div class="resource">
        <h3 class="resource__name">Memory Allies | Alliance for Indigenous Elders</h3>
        <p>An interactive educational program to better understand what dementia is and how it affects people.</p>
        <p>https://indigenouselders.org/memory-allies/</p>
      </div>
      <div class="resource">
        <h3 class="resource__name">Caring for a Grandchild</h3>
        <p>Grandparents Raising<br>Grandchildren (Kinship Care)</p>
      </div>
      <div class="resource">
        <h3 class="resource__name">KinshipHomes.org</h3>
        <p>An interactive website that seeks to share all relevant publicly available information impacting grandfamilies.</p>
      </div>
      <div class="resource">
        <h3 class="resource__name">Grandparent Resources | Tribal Elder Justice Network</h3>
        <p>A list of resources for grandparents<br>raising grandchildren.</p>
        <p>https://indigenouselders.org/tejn/<br>grandparent-resources/</p>
      </div>
    </div>
  </div>
</section>

</body>
</html>
```